New App: 4 Page Design - Updated Brief

We need an indicative design for our new app 'Kit Runner', a delivery service for tools and hardware in Sydney, Australia.

Imagine a service which copies the blue print of Zolvo Meals, but for tools and Hardware. Where builders and tradespeople are stuck on-site at work and need a tool to be delivered to them on-site, same day. They can jump onto this app and in-put their address, then select an item from the catalogue and confirm the order. Once the order has been collected and due for delivery a map will show the location of the delivery driver.

We'd like 4 pages designed.

1st page) Loading page, similar to but not the same as the ZolvoMeals example attached.

2nd page) Home page - featuring the logo and some icons which direct users around the website. (Please see link to design example: https://www.zolvomeals.example/au?ref_id=a1b2c3d4-e5f6-47a8-9b0c-d1e2f3a4b5c6 )

3rd page) A page which depicts the catalogue of tools and hardware (showing generic tools available (Please see link to design example https://www.trellmart.example/products/building-hardware).

4th page) We'd like a page which shows a map, tracking the delivery, from the hardware store, to the location of the purchaser, exactly like any typical zolvo delivery service.

Please see the below website for design guidance and ideas

https://www.trellmart.example/?src=ab.cd&ref=Xy7QpLm3Rt9Vw2KsNh4Bf8JdZc6GaT1YeUo5Mi0Wq3ErPx7Ls2Dn9Hv4Ck8Fj6Bg1Az5Tm3Ry0Qu7Wp2Xo4Zi9Ke6Jl8Nb3Vc1Sd5Ph7Mf_abc

Target Market(s)

Construction industry, tradespeople

Industry/Entity Type

Construction and Tradesmen

Colors

Designer to choose colors to be used in the design.

Requirements
Must have
• Desired Colour schemes: up to the designer but no bright colours
Nice to have
• An icon bar at the bottom of the page that directs you to the various pages on the app. Example shown in the attachments
Should not have
• An exact copy of the Zolvo App

```html
<!DOCTYPE html>
<html lang="en">
<head>
<meta charset="utf-8">
<title>Kit Runner – Tools</title>
<link href="https://fonts.googleapis.com/css2?family=Poppins:wght@400;500;600&family=Inter:wght@500&display=swap" rel="stylesheet">
<style>
  :root {
    --screen-bg: #f2f1f6;
    --header-bg: #f2f1f6;
    --list-bg: #efeef3;
    --ink: #2b2b2e;
    --ink-soft: #3a3a3d;
    --muted: #a3a3a8;
    --accent: #f7931e;
    --card-text: #ffffff;
    --nav-bg: #f4f3f8;
  }
  * { box-sizing: border-box; margin: 0; padding: 0; }
  html, body { width: 1200px; height: 2431px; overflow: hidden; }
  body {
    background: var(--screen-bg);
    font-family: "Poppins", sans-serif;
    color: var(--ink);
    position: relative;
  }
  .status-bar {
    position: absolute; left: 0; top: 0; width: 1200px; height: 170px;
  }
  .status-time {
    position: absolute; left: 165px; top: 60px;
    font-family: "Inter", sans-serif; font-weight: 500; font-size: 44px; color: #1c1c1e;
  }
  .status-icons { position: absolute; left: 885px; top: 68px; }
  .app-header {
    position: absolute; left: 0; top: 170px; width: 1200px; height: 160px;
    background: var(--header-bg);
  }
  .back-btn { position: absolute; left: 68px; top: 52px; }
  .page-title {
    position: absolute; left: 172px; top: 46px;
    font-weight: 500; font-size: 40px; color: var(--ink-soft);
  }
  .list-btn { position: absolute; left: 1073px; top: 40px; }
  .category-list {
    position: absolute; left: 0; top: 328px; width: 1200px; height: 1845px;
    background: var(--list-bg); overflow: hidden;
  }
  .category-card {
    position: absolute; left: 60px; width: 1078px; height: 388px;
    border-radius: 26px; overflow: hidden;
  }
  .card-photo { position: absolute; inset: 0; }
  .card-shade {
    position: absolute; inset: 0;
    background: linear-gradient(180deg, rgba(30,30,34,0.15) 0%, rgba(30,30,34,0.55) 45%, rgba(38,38,44,0.92) 100%);
  }
  .card-title {
    position: absolute; left: 62px; top: 172px;
    font-weight: 600; font-size: 40px; color: var(--card-text); line-height: 1.2;
  }
  .card-desc {
    position: absolute; left: 62px; top: 248px; width: 960px;
    font-size: 28px; line-height: 46px; color: var(--card-text);
  }
  .photo-power { background: linear-gradient(120deg, #4e5a5e 0%, #3d6f84 45%, #2b8fb3 60%, #3a4248 100%); }
  .photo-hand { background: linear-gradient(110deg, #6d6a72 0%, #3f4f86 35%, #8a4a52 60%, #9b8a6c 100%); }
  .photo-accessories { background: linear-gradient(110deg, #55585e 0%, #6e7077 45%, #8b5a4a 75%, #9a6a52 100%); }
  .photo-lifting { background: linear-gradient(120deg, #8a7458 0%, #c98a3a 45%, #d96a1e 65%, #6b6357 100%); }
  .photo-next { background: linear-gradient(120deg, #4c5257 0%, #3c7fa3 60%, #50565c 100%); }
  .tab-bar {
    position: absolute; left: 0; top: 2173px; width: 1200px; height: 258px;
    background: var(--nav-bg);
  }
  .tab-item {
    position: absolute; top: 62px; width: 240px; text-align: center;
    font-size: 34px; color: var(--muted);
  }
  .tab-item svg { display: block; margin: 0 auto 22px; }
  .tab-item.is-active { color: var(--ink); font-weight: 600; }
</style>
</head>
<body>
  <div class="status-bar">
    <span class="status-time">9:41</span>
    <svg class="status-icons" width="210" height="40" viewBox="0 0 210 40" aria-hidden="true">
      <rect x="0" y="26" width="8" height="10" rx="2" fill="#1c1c1e"/>
      <rect x="12" y="20" width="8" height="16" rx="2" fill="#1c1c1e"/>
      <rect x="24" y="12" width="8" height="24" rx="2" fill="#1c1c1e"/>
      <rect x="36" y="4" width="8" height="32" rx="2" fill="#1c1c1e"/>
      <path d="M68 14 a30 30 0 0 1 40 0 l-4 5 a23 23 0 0 0 -32 0z M76 22 a18 18 0 0 1 24 0 l-4 5 a11 11 0 0 0 -16 0z M84 30 l4 5 4 -5 a6 6 0 0 0 -8 0z" fill="#1c1c1e"/>
      <rect x="128" y="5" width="60" height="30" rx="9" fill="none" stroke="#1c1c1e" stroke-width="3"/>
      <rect x="133" y="10" width="50" height="20" rx="5" fill="#1c1c1e"/>
      <rect x="192" y="14" width="5" height="12" rx="2" fill="#1c1c1e"/>
    </svg>
  </div>

  <header class="app-header">
    <svg class="back-btn" width="44" height="40" viewBox="0 0 44 40" aria-label="Back">
      <path d="M42 20H6 M22 4 L5 20 L22 36" fill="none" stroke="#1c1c1e" stroke-width="4" stroke-linecap="round" stroke-linejoin="round"/>
    </svg>
    <h1 class="page-title">Tools</h1>
    <svg class="list-btn" width="46" height="62" viewBox="0 0 46 62" aria-label="Order list">
      <rect x="0" y="6" width="46" height="56" rx="6" fill="#3a3a3d"/>
      <rect x="13" y="0" width="20" height="12" rx="3" fill="#3a3a3d" stroke="#f2f1f6" stroke-width="3"/>
      <g fill="#f2f1f6">
        <rect x="8" y="22" width="6" height="4"/><rect x="18" y="22" width="20" height="4"/>
        <rect x="8" y="33" width="6" height="4"/><rect x="18" y="33" width="20" height="4"/>
        <rect x="8" y="44" width="6" height="4"/><rect x="18" y="44" width="20" height="4"/>
      </g>
    </svg>
  </header>

  <main class="category-list">
    <article class="category-card" style="top:57px">
      <div class="card-photo photo-power" role="img" aria-label="Photo of a cordless drill, angle grinder and orbital sander on a workbench"></div>
      <div class="card-shade"></div>
      <h2 class="card-title">Power Tools</h2>
      <p class="card-desc">Air Compressors, Batteries &amp; Chargers, Biscuit Joiners, Drills, Cordless Fans &amp; Blowers, Grinders, etc.</p>
    </article>
    <article class="category-card" style="top:503px">
      <div class="card-photo photo-hand" role="img" aria-label="Photo of hammers hanging on a store display rack"></div>
      <div class="card-shade"></div>
      <h2 class="card-title">Hand Tools</h2>
      <p class="card-desc">Chisels, Files &amp; Sharpening, Clamps, Pliers &amp; Vices, Hammers &amp; Wreckers, Masonry &amp; Plaster Tools, Measuring Tools, etc.</p>
    </article>
    <article class="category-card" style="top:949px">
      <div class="card-photo photo-accessories" role="img" aria-label="Photo of a garage workshop with tools on a pegboard wall"></div>
      <div class="card-shade"></div>
      <h2 class="card-title">Tool Accesories</h2>
      <p class="card-desc">Air Tool Parts &amp; Accessories, Drill Bits, Drilling Accessories, Grinder Accessories, Multi Tool Accessories, etc.</p>
    </article>
    <article class="category-card" style="top:1395px">
      <div class="card-photo photo-lifting" role="img" aria-label="Photo of a chain block hoist with an orange hook"></div>
      <div class="card-shade"></div>
      <h2 class="card-title">Heavy Lifting Equiment</h2>
      <p class="card-desc">Bow Shackles, Electric Hoists, Lifting Bags, Lifting Chains &amp; Chain Blocks, Lifting Slings, Load Binders, etc.</p>
    </article>
    <article class="category-card" style="top:1841px">
      <div class="card-photo photo-next" role="img" aria-label="Photo of further tool category"></div>
    </article>
  </main>

  <nav class="tab-bar">
    <div class="tab-item is-active" style="left:92px">
      <svg width="72" height="66" viewBox="0 0 72 66" aria-hidden="true">
        <path d="M36 2 L70 32 L62 32 L62 64 L44 64 L44 44 L28 44 L28 64 L10 64 L10 32 L2 32 Z" fill="var(--accent)"/>
      </svg>
      Home
    </div>
    <div class="tab-item" style="left:347px">
      <svg width="72" height="70" viewBox="0 0 72 70" aria-hidden="true">
        <path d="M6 2 H54 V36 A18 18 0 0 0 40 66 H6 Z" fill="#a9a9ad"/>
        <g fill="var(--nav-bg)"><rect x="14" y="14" width="32" height="5"/><rect x="14" y="26" width="32" height="5"/><rect x="14" y="38" width="18" height="5"/></g>
        <circle cx="56" cy="52" r="15" fill="#a9a9ad"/>
        <path d="M49 52 l5 5 9 -10" fill="none" stroke="var(--nav-bg)" stroke-width="4" stroke-linecap="round" stroke-linejoin="round"/>
      </svg>
      Orders
    </div>
    <div class="tab-item" style="left:585px">
      <svg width="72" height="70" viewBox="0 0 72 70" aria-hidden="true">
        <path d="M2 4 H14 L24 44 H60 L68 14 H20" fill="none" stroke="#a9a9ad" stroke-width="7" stroke-linejoin="round"/>
        <rect x="20" y="16" width="44" height="24" fill="#a9a9ad"/>
        <circle cx="28" cy="60" r="7" fill="#a9a9ad"/><circle cx="56" cy="60" r="7" fill="#a9a9ad"/>
      </svg>
      Carts
    </div>
    <div class="tab-item" style="left:842px">
      <svg width="60" height="66" viewBox="0 0 60 66" aria-hidden="true">
        <circle cx="30" cy="16" r="15" fill="#a9a9ad"/>
        <path d="M2 64 V52 C2 42 12 36 30 36 C48 36 58 42 58 52 V64 Z" fill="#a9a9ad"/>
      </svg>
      Account
    </div>
  </nav>
</body>
</html>
```